Business Cards Design for the electrical wholesaler: clean bold dynamic :)

We need a business card design that would follow our latest brand guidelines. As an electrical wholesaler we want to bring a fresh look and feel into the industry. The design should be clean bold and dynamic. It should come alive with the renewed energy of our green colour. Our grey colour should keep things balanced and complement the notion of maturity and responsibility. We employ Lato as a corporate font however are not bound by this font and we’re open to interpretation here.

Target Market(s)

Electrical contractors

Industry/Entity Type

Business

Contact Information for Business Card

Logo
Name & Surname: Halyna Dorosh
Job Title: Director of Marketing
Email: halya.dorosh@quillmail.example
Cell phone: XXX.XXX.XXXX
Address: 20517 - 87 Ave. Edmonton, AB, Canada. T6K 4N8
Business Phone: 780.555.0184
Website: www.brovix.example

Font styles to use
Other font styles liked:
• Lato

Requirements
Must have
• Logo & website
Nice to have
• Brand elements - some of them you may find in the attached Brand Guidelines (e.g. three lines on the background signifying "W")

```html
<!DOCTYPE html>
<html lang="en">
<head>
<meta charset="utf-8">
<title>brovix business cards</title>
<link rel="stylesheet" href="https://fonts.googleapis.com/css2?family=Work+Sans:wght@400;500&display=swap">
<style>
  :root {
    --bg: #1c1c1c;
    --card: #232323;
    --card-edge: #2c2c2c;
    --text-light: #eaeaea;
    --logo-grey: #bdbdbd;
    --mark-grey: #3a3a3a;
    --green: #7dc242;
  }
  * { margin: 0; padding: 0; box-sizing: border-box; }
  html, body { width: 1200px; height: 900px; overflow: hidden; }
  body {
    background: var(--bg);
    font-family: "Work Sans", sans-serif;
    position: relative;
  }
  .card {
    position: absolute;
    left: 280px;
    width: 640px;
    height: 366px;
    background: linear-gradient(135deg, var(--card) 0%, var(--card-edge) 100%);
    box-shadow: 0 18px 40px rgba(0,0,0,0.55);
    overflow: hidden;
  }
  .card--front { top: 60px; }
  .card--back { top: 474px; }

  .brand {
    display: flex;
    align-items: center;
    gap: 14px;
  }
  .brand__square {
    width: 40px;
    height: 40px;
    background: var(--mark-grey);
  }
  .brand__name {
    font-weight: 500;
    color: var(--logo-grey);
    letter-spacing: 0.5px;
    line-height: 1;
  }
  .card--front .brand {
    position: absolute;
    left: 50%;
    top: 50%;
    transform: translate(-50%, -50%);
  }
  .card--front .brand__name { font-size: 64px; }
  .card--front .brand__square { width: 54px; height: 54px; gap: 16px; }

  .card--back .brand {
    position: absolute;
    left: 40px;
    top: 156px;
  }
  .card--back .brand__name { font-size: 46px; }

  .divider {
    position: absolute;
    left: 276px;
    top: 86px;
    width: 2px;
    height: 196px;
    background: var(--green);
  }
  .contact {
    position: absolute;
    left: 300px;
    top: 84px;
    color: var(--text-light);
  }
  .contact__name {
    font-size: 26px;
    font-weight: 500;
    color: var(--green);
    letter-spacing: 0.8px;
    line-height: 1.1;
  }
  .contact__title {
    font-size: 16px;
    letter-spacing: 0.6px;
    margin-bottom: 12px;
  }
  .contact__address {
    font-size: 16px;
    letter-spacing: 0.5px;
    line-height: 1.35;
    margin-bottom: 10px;
  }
  .contact__list { list-style: none; }
  .contact__item {
    display: flex;
    align-items: center;
    gap: 11px;
    font-size: 16px;
    letter-spacing: 0.5px;
    line-height: 1.55;
    white-space: nowrap;
  }
  .contact__icon { width: 13px; height: 13px; flex: none; }
</style>
</head>
<body>
  <section class="card card--front" aria-label="Card front">
    <div class="brand">
      <span class="brand__square"></span>
      <span class="brand__name">brovix</span>
    </div>
  </section>

  <section class="card card--back" aria-label="Card back">
    <div class="brand">
      <span class="brand__square"></span>
      <span class="brand__name">brovix</span>
    </div>
    <div class="divider"></div>
    <div class="contact">
      <p class="contact__name">Halyna Dorosh</p>
      <p class="contact__title">Director of Marketing</p>
      <p class="contact__address">20517 - 87 Ave.<br>Edmonton, AB, Canada. T6K 4N8</p>
      <ul class="contact__list">
        <li class="contact__item">
          <svg class="contact__icon" viewBox="0 0 16 16" aria-hidden="true"><path d="M3 1h3l1.5 4-2 1.5a9 9 0 0 0 4 4L11 8.5l4 1.5v3a2 2 0 0 1-2 2A12 12 0 0 1 1 3a2 2 0 0 1 2-2z" fill="var(--green)"/></svg>
          <span>780.555.0184</span>
        </li>
        <li class="contact__item">
          <svg class="contact__icon" viewBox="0 0 16 16" aria-hidden="true"><rect x="1" y="3" width="14" height="10" fill="none" stroke="var(--green)" stroke-width="1.6"/><path d="M1 3l7 6 7-6" fill="none" stroke="var(--green)" stroke-width="1.6"/></svg>
          <span>halya.dorosh@quillmail.example</span>
        </li>
        <li class="contact__item">
          <svg class="contact__icon" viewBox="0 0 16 16" aria-hidden="true"><g fill="none" stroke="var(--green)" stroke-width="1.4"><circle cx="8" cy="8" r="6.5"/><ellipse cx="8" cy="8" rx="2.8" ry="6.5"/><path d="M1.5 8h13"/></g></svg>
          <span>www.brovix.example</span>
        </li>
      </ul>
    </div>
  </section>
</body>
</html>
```